Flyer-Design für Shop für nachhaltige Haustierprodukte
LOMERU
Tolle Umsetzung nach den Vorgaben. Änderungen super und schnell umgesetzt. Gerne wieder!
Zielgruppe
LOMERU ist ein Online-Marktplatz für nachhaltige Haustierprodukte. Meine Zielgruppe sind Frauen zwischen 30 und 60 Jahren mit Haustieren (Hund, Katze, Pferd)
Aufgabenstellung
Das Design soll an der Webseite angepasst sein. Es ist wichtig, dass das Thema Nachhaltigkeit kommuniziert wird und welche Vorteile LOMERU hat (Markenvielvalt, kleine Manufakturen, Handmade etc.)

```html
<!DOCTYPE html>
<html lang="de">
<head>
<meta charset="utf-8">
<title>LOMERU Flyer</title>
<link rel="stylesheet" href="https://fonts.googleapis.com/css2?family=Oswald:wght@400;500&family=Raleway:wght@400;600;700&display=swap">
<style>
  :root {
    --bg: #ecebdf;
    --paper: #fbfbf9;
    --panel-grey: #e2e2dd;
    --orange: #ee7a2e;
    --orange-light: #f9c9a6;
    --orange-deep: #f0a06c;
    --ink: #454545;
    --ink-soft: #6b6b6b;
    --bar: #4a4a4a;
  }
  * { box-sizing: border-box; margin: 0; padding: 0; }
  html, body { width: 799px; height: 1200px; overflow: hidden; background: var(--bg); }
  body { font-family: "Raleway", sans-serif; color: var(--ink); position: relative; }

  .spread { position: absolute; left: 20px; width: 759px; height: 537px; display: flex; box-shadow: 0 4px 14px rgba(0,0,0,0.08); }
  .spread--inside { top: 40px; }
  .spread--outside { top: 623px; }
  .panel { position: relative; width: 253px; height: 100%; overflow: hidden; background: var(--paper); }

  .photo { position: absolute; left: 0; width: 100%; }
  .heading { font-family: "Oswald", sans-serif; font-weight: 500; text-transform: uppercase; letter-spacing: 3px; color: var(--ink); line-height: 1.15; }
  .heading em { font-style: normal; color: var(--orange); }
  .accent-bar { position: absolute; width: 5px; height: 20px; background: var(--bar); }
  .body-text { font-size: 8px; line-height: 1.5; color: var(--ink-soft); }
  .list-item { margin-bottom: 9px; font-size: 7.6px; line-height: 1.45; color: var(--ink-soft); }
  .list-item strong { display: block; font-weight: 700; color: var(--ink); font-size: 8.2px; }

  /* inside */
  .mission .photo { top: 0; height: 300px; background: linear-gradient(160deg, #e7e3bf 0%, #cfc78a 40%, #b9a96c 70%, #d8d2b4 100%); }
  .mission .heading { position: absolute; left: 28px; top: 318px; font-size: 18px; }
  .mission .accent-bar { left: 28px; top: 356px; }
  .mission .body-text { position: absolute; left: 44px; top: 352px; width: 185px; }
  .mission .body-text p { margin-bottom: 8px; }

  .criteria-a { background: var(--panel-grey); }
  .criteria-b { background: var(--paper); }
  .criteria-title { position: absolute; left: 273px; top: 62px; font-size: 19px; white-space: nowrap; z-index: 2; }
  .criteria-a .accent-bar { left: 26px; top: 112px; }
  .criteria-a .list { position: absolute; left: 42px; top: 108px; width: 190px; }
  .criteria-b .list { position: absolute; left: 26px; top: 108px; width: 200px; }
  .animals-band { position: absolute; left: 253px; bottom: 0; width: 506px; height: 188px; background: linear-gradient(100deg, #8a7258 0%, #b49a7c 30%, #cfc3b2 55%, #e6e2dc 80%, #f1f0ec 100%); }

  /* outside */
  .why { background: #f0f0ec; }
  .why .photo { top: 0; height: 200px; background: linear-gradient(170deg, #d4d6d2 0%, #c8c4ac 45%, #c5b98e 75%, #d7cd7c 100%); }
  .why .heading { position: absolute; left: 26px; top: 218px; font-size: 17px; }
  .why .accent-bar { left: 26px; top: 268px; }
  .why .list { position: absolute; left: 42px; top: 266px; width: 192px; }

  .contact { background: linear-gradient(180deg, var(--orange-light) 0%, #f6b58a 55%, var(--orange-deep) 100%); }
  .contact .rule { position: absolute; left: 0; top: 40px; width: 22px; height: 3px; background: var(--bar); }
  .contact .heading { position: absolute; left: 32px; top: 30px; font-size: 15px; font-style: italic; font-weight: 400; color: #8a8a8a; letter-spacing: 3.5px; }
  .contact-list { position: absolute; left: 32px; top: 88px; list-style: none; }
  .contact-list li { display: flex; align-items: center; gap: 10px; margin-bottom: 12px; font-size: 8px; color: #6b6b6b; }
  .contact-list svg { width: 18px; height: 18px; flex: none; }

  .cover { background: var(--paper); text-align: center; }
  .brand-name { position: absolute; left: 0; width: 100%; top: 48px; font-family: "Raleway", sans-serif; font-weight: 600; font-size: 40px; letter-spacing: 4px; color: var(--orange); }
  .brand-dot { position: absolute; left: 101px; top: 108px; width: 50px; height: 50px; border-radius: 50%; border: 2px solid var(--orange); }
  .cover .photo { left: 37px; top: 182px; width: 180px; height: 176px; background: linear-gradient(150deg, #eef0ea 0%, #c9d3b8 40%, #c49a6a 70%, #e4d9c8 100%); }
  .cover .rule { position: absolute; left: 112px; top: 372px; width: 30px; height: 3px; background: var(--bar); }
  .site-name { position: absolute; left: 0; width: 100%; top: 382px; font-family: "Oswald", sans-serif; font-weight: 500; font-size: 17px; letter-spacing: 3px; color: var(--ink); }
  .tagline { position: absolute; left: 0; width: 100%; top: 410px; font-size: 10.5px; line-height: 1.35; color: var(--ink); }
  .tagline span { color: var(--orange); }
</style>
</head>
<body>

<section class="spread spread--inside">
  <div class="panel mission">
    <div class="photo" role="img" aria-label="Foto: Hund sitzt in einer Wiese mit gelben Blumen"></div>
    <h2 class="heading">Unsere <em>Mission</em></h2>
    <span class="accent-bar"></span>
    <div class="body-text">
      <p>LOMA und ich, Ruth sind die Gründerinnen von LOMERU – daher auch der Name.</p>
      <p>Unsere Mission ist es, mit einer ehrlichen Online-Plattform fair und ökologisch hergestellte Haustierprodukte sichtbar zu machen. Damit unterstützen wir das nachhaltige Leben mit Haustieren und reduzieren ihren ökologischen Fußabdruck.</p>
    </div>
  </div>

  <div class="panel criteria-a">
    <span class="accent-bar"></span>
    <div class="list">
      <div class="list-item"><strong>Made in Germany</strong>Produkte stammen von Herstellern, die in Deutschland produzieren.</div>
      <div class="list-item"><strong>Nachhaltige Verpackung</strong>Verpackung ist z.B. plastikfrei oder komplett recyclebar</div>
      <div class="list-item"><strong>Handgemacht</strong>Produkte sind handgefertigt</div>
      <div class="list-item"><strong>Upcycling</strong>Produkte, die aus recycelten Materialien hergestellt wurden.</div>
      <div class="list-item"><strong>Recyclingfähig</strong>Produkte sind vollständig recyclebar</div>
    </div>
  </div>

  <div class="panel criteria-b">
    <div class="list">
      <div class="list-item"><strong>Fair produziert</strong>Produkte aus fairer Herstellung z.B. durch gerechte Bezahlungen und faire Arbeitsbedingungen</div>
      <div class="list-item"><strong>Soziale Unterstützung</strong>Produkte, die bei der Herstellung oder dem Verkauf soziale Einrichtungen unterstützen.</div>
      <div class="list-item"><strong>BIO-Zertifiziert</strong>Produkte enthalten Inhalte aus biologischem Anbau.</div>
      <div class="list-item"><strong>Beitrag zum Umweltschutz</strong>Hersteller leistet einen Beitrag zum Umweltschutz.</div>
      <div class="list-item"><strong>Verzicht auf Massentierhaltung</strong>Produkte enthalten kein Fleisch aus Massentierhaltung.</div>
    </div>
  </div>

  <h2 class="heading criteria-title">Unsere <em>Nachhaltig</em>keitskriterien</h2>
  <div class="animals-band" role="img" aria-label="Foto: Katze und Fohlen schmiegen sich aneinander"></div>
</section>

<section class="spread spread--outside">
  <div class="panel why">
    <div class="photo" role="img" aria-label="Foto: Ponys grasen auf einer Blumenwiese"></div>
    <h2 class="heading">Warum <em>nachhaltige</em><br>Haustierprodukte?</h2>
    <span class="accent-bar"></span>
    <div class="list">
      <div class="list-item"><strong>Fair &amp; Ökologisch</strong>Hersteller achten bei der Produktion auf eine geringe Umweltbelastung und lassen ihre Mitarbeiter und Lieferanten fair bezahlen</div>
      <div class="list-item"><strong>Manufakturen</strong>Viele Produkte stammen aus kleineren Manufakturen, die mit viel Herzblut und Leidenschaft Haustierprodukte herstellen</div>
      <div class="list-item"><strong>Schadstofffrei</strong>Produkte enthalten keine Chemie oder Schadstoffe, die deinem Haustier schaden können</div>
      <div class="list-item"><strong>Verpackung</strong>Von der Produktverpackung bis hin zum Versandkarton: Nachhaltig Verpackt</div>
      <div class="list-item"><strong>Preis-Leistung</strong>Qualitativ hochwertige Produkte mit langer Lebensdauer</div>
    </div>
  </div>

  <div class="panel contact">
    <span class="rule"></span>
    <h2 class="heading">So findet ihr uns</h2>
    <ul class="contact-list">
      <li><svg viewBox="0 0 18 18"><circle cx="9" cy="9" r="8.5" fill="#8a8a8a"/><path d="M6 5.2l1.6-.4 1 2.2-1 .8a6 6 0 002.6 2.6l.8-1 2.2 1-.4 1.6c-3.4.2-7-3.4-6.8-6.8z" fill="#f7c4a0"/></svg>+49 1570 4432 219</li>
      <li><svg viewBox="0 0 18 18"><circle cx="9" cy="9" r="8.5" fill="#8a8a8a"/></svg>LOMERUDE</li>
      <li><svg viewBox="0 0 18 18"><circle cx="9" cy="9" r="8.5" fill="#8a8a8a"/></svg>lomeru.de</li>
      <li><svg viewBox="0 0 18 18"><circle cx="9" cy="9" r="8.5" fill="#8a8a8a"/><circle cx="9" cy="9" r="4.5" fill="none" stroke="#f7c4a0" stroke-width="1"/><path d="M4.5 9h9M9 4.5c-2 2.5-2 6.5 0 9M9 4.5c2 2.5 2 6.5 0 9" fill="none" stroke="#f7c4a0" stroke-width="0.8"/></svg>www.lomeru.de</li>
      <li><svg viewBox="0 0 18 18"><circle cx="9" cy="9" r="8.5" fill="#8a8a8a"/><rect x="4.5" y="6" width="9" height="6.5" fill="none" stroke="#f7c4a0" stroke-width="1"/><path d="M4.5 6l4.5 3.8L13.5 6" fill="none" stroke="#f7c4a0" stroke-width="1"/></svg>info@lomeru.de</li>
    </ul>
  </div>

  <div class="panel cover">
    <div class="brand-name">LOMERU</div>
    <span class="brand-dot"></span>
    <div class="photo" role="img" aria-label="Foto: zwei fröhliche Hunde laufen durch Gräser"></div>
    <span class="rule"></span>
    <div class="site-name">LOMERU.DE</div>
    <p class="tagline">Dein neuer Online-Marktplatz für<br><span>nachhaltige Haustierprodukte</span></p>
  </div>
</section>

</body>
</html>
```